TeaLantern Flyer

I require an A5 sized flyer to be designed that advertised the new flexible workspace of TeaLantern.
should say it is a "Flexible Workspace with EV Charging"
web address is www.tealantern.co.uk
It should show the 3 different types of membership as priced on the website

```html
<!DOCTYPE html>
<html lang="en">
<head>
<meta charset="utf-8">
<title>TeaLantern Flyer</title>
<link href="https://fonts.googleapis.com/css2?family=Poppins:wght@400;500;600;700&family=Russo+One&display=swap" rel="stylesheet">
<style>
:root{
  --orange:#f39200;
  --ink:#2b2b2b;
  --card:#2d2d2d;
  --card-mid:#3c3c3c;
  --paper:#ffffff;
  --mist:#ececec;
  --muted:#cfcfcf;
}
*{box-sizing:border-box;margin:0;padding:0}
html,body{width:800px;height:1200px;overflow:hidden;background:var(--paper)}
.flyer{position:relative;width:800px;height:1200px;background:var(--paper);font-family:"Poppins",sans-serif;color:var(--ink);overflow:hidden}
.art{position:absolute;inset:0}
.brand{position:absolute;left:173px;top:0;width:443px;height:105px;display:flex;align-items:center;justify-content:center;font-family:"Poppins",sans-serif;font-weight:700;font-size:44px;color:var(--paper);letter-spacing:.5px}
.display{font-family:"Russo One",sans-serif;font-style:italic}
.headline-flexible{position:absolute;top:128px;left:0;width:800px;text-align:center;font-size:50px;font-weight:400;color:var(--orange);padding-left:4px}
.headline-workspace{position:absolute;top:184px;left:120px;font-size:80px;color:var(--ink);letter-spacing:1px;line-height:1}
.tag-with{position:absolute;left:610px;top:208px;width:103px;height:46px;border-radius:6px;background:var(--orange);color:var(--paper);font-family:"Poppins",sans-serif;font-weight:700;font-size:34px;line-height:46px;text-align:center}
.headline-ev{position:absolute;left:456px;top:296px;font-size:44px;color:var(--ink)}
.tier-title{position:absolute;top:712px;display:flex;align-items:center;gap:12px}
.tier-title svg{width:42px;height:42px;flex:none}
.tier-name{font-family:"Russo One",sans-serif;font-style:italic;font-size:26px;line-height:26px}
.tier-name span{display:block}
.tier-name .top{color:var(--ink)}
.tier-name .bottom{color:var(--orange)}
.card{position:absolute;top:783px;width:212px;height:320px;border-radius:6px;background:var(--card);color:var(--paper);padding:30px 6px 0 16px}
.card.mid{background:var(--card-mid)}
.perks{list-style:none;font-size:11px;line-height:14px;letter-spacing:-.1px}
.perks li{position:relative;padding-left:9px;margin-bottom:5px;white-space:nowrap}
.perks li::before{content:"";position:absolute;left:0;top:6px;width:3px;height:3px;border-radius:50%;background:var(--orange)}
.perks small{display:block;font-size:8.5px;line-height:10px}
.price{position:absolute;left:0;right:0;display:flex;justify-content:center;align-items:center;gap:8px}
.pill{background:var(--orange);border-radius:6px;color:var(--paper);font-family:"Russo One",sans-serif;font-style:italic;font-size:30px;line-height:40px;padding:0 8px;display:inline-flex;align-items:flex-start}
.pill sup{font-size:14px;line-height:20px;margin-right:1px}
.price-note{font-family:"Russo One",sans-serif;font-style:italic;font-size:15px;line-height:14px}
.plus{width:24px;height:24px;border-radius:50%;background:var(--paper);color:var(--ink);font-weight:700;font-size:20px;line-height:23px;text-align:center;margin:0 -4px;z-index:1}
.price-sub{position:absolute;left:0;right:0;text-align:center;font-size:10px;color:var(--muted)}
.price-labels{position:absolute;left:0;right:0;display:flex;justify-content:center;gap:22px;font-family:"Russo One",sans-serif;font-style:italic;font-size:14px}
.footer{position:absolute;top:1134px;left:52px;right:50px;display:flex;align-items:center}
.email{display:flex;align-items:center;gap:6px;font-size:17px;font-weight:500;font-style:italic;color:var(--ink)}
.divider{width:3px;height:30px;background:var(--orange);margin:0 18px 0 22px}
.web{font-family:"Russo One",sans-serif;font-style:italic;font-size:24px;letter-spacing:4px;color:var(--ink)}
.web b{font-weight:400;color:var(--orange)}
</style>
</head>
<body>
<main class="flyer">
  <svg class="art" viewBox="0 0 800 1200" aria-hidden="true">
    <defs>
      <linearGradient id="band" x1="0" x2="1" y1="0" y2="0">
        <stop offset="0" stop-color="#ffffff"/>
        <stop offset="1" stop-color="#e4e4e4"/>
      </linearGradient>
      <linearGradient id="base" x1="0" x2="0" y1="0" y2="1">
        <stop offset="0" stop-color="#ffffff"/>
        <stop offset="1" stop-color="#e6e6e6"/>
      </linearGradient>
    </defs>
    <path d="M173 0 H616 L580 80 Q570 105 545 105 H245 Q220 105 210 80 Z" fill="#2f2f2f"/>
    <rect x="0" y="274" width="208" height="5" fill="var(--orange)"/>
    <rect x="390" y="270" width="410" height="86" fill="url(#band)"/>
    <rect x="0" y="1055" width="800" height="145" fill="url(#base)"/>
  </svg>

  <svg class="art" viewBox="0 0 800 1200" role="img" aria-label="Photo of a hand plugging a charging cable into an electric car">
    <defs>
      <linearGradient id="evPhoto" x1="0" x2="1" y1="0" y2="1">
        <stop offset="0" stop-color="#6f7a5a"/>
        <stop offset=".5" stop-color="#a9aca4"/>
        <stop offset="1" stop-color="#e9eaea"/>
      </linearGradient>
    </defs>
    <path d="M0 297 H390 C345 330 325 395 305 440 C292 470 265 478 235 478 H0 Z" fill="url(#evPhoto)"/>
  </svg>

  <svg class="art" viewBox="0 0 800 1200" role="img" aria-label="Photo of the open-plan workspace with tables, chairs and a wood floor">
    <defs>
      <linearGradient id="officePhoto" x1="0" x2="0" y1="0" y2="1">
        <stop offset="0" stop-color="#dcdcd8"/>
        <stop offset=".35" stop-color="#b8b2a8"/>
        <stop offset=".58" stop-color="#7c5f47"/>
        <stop offset=".75" stop-color="#6b6b6b"/>
        <stop offset="1" stop-color="#5a5a5a"/>
      </linearGradient>
    </defs>
    <path d="M420 356 H800 V688 H56 L225 494 C270 494 302 482 318 446 C336 405 360 366 420 356 Z" fill="url(#officePhoto)"/>
    <path d="M56 688 L225 494" stroke="#333" stroke-width="6"/>
    <rect x="56" y="686" width="744" height="5" fill="#333"/>
    <path d="M398 297 C352 330 332 398 314 446 C300 482 272 493 240 493 H0" fill="none" stroke="var(--orange)" stroke-width="6"/>
  </svg>

  <div class="brand">TeaLantern</div>
  <h1 class="headline-flexible display">Flexible</h1>
  <div class="headline-workspace display">Workspace</div>
  <div class="tag-with">with</div>
  <div class="headline-ev display">EV Charging</div>

  <div class="tier-title" style="left:50px">
    <svg viewBox="0 0 42 42" fill="none" stroke="#2b2b2b" stroke-width="2.2" stroke-linecap="round">
      <circle cx="21" cy="21" r="8"/>
      <path d="M21 4v5M21 33v5M4 21h5M33 21h5M9 9l3.5 3.5M29.5 29.5 33 33M9 33l3.5-3.5M29.5 12.5 33 9"/>
    </svg>
    <div class="tier-name"><span class="top">DAY</span><span class="bottom">MEMBER</span></div>
  </div>
  <div class="tier-title" style="left:290px">
    <svg viewBox="0 0 42 42" fill="none" stroke="#2b2b2b" stroke-width="2.2" stroke-linecap="round">
      <circle cx="16" cy="15" r="6"/>
      <path d="M5 34c0-7 5-11 11-11 3 0 6 1 8 3"/>
      <circle cx="28" cy="11" r="5"/>
      <path d="M30 28v10M25 33h10"/>
    </svg>
    <div class="tier-name"><span class="top">LIGHT</span><span class="bottom">MEMBER</span></div>
  </div>
  <div class="tier-title" style="left:524px">
    <svg viewBox="0 0 42 42" fill="none" stroke="#2b2b2b" stroke-width="2.2" stroke-linecap="round" stroke-linejoin="round">
      <circle cx="30" cy="12" r="6"/>
      <path d="M26 16 16 26M19 23l3 3M16 26l3 3"/>
      <path d="M3 30h8l6 4h10c2 0 2-3 0-3h-8M27 32l9-5c2-1 3 1 2 3l-10 7H3"/>
    </svg>
    <div class="tier-name"><span class="top">ALL ACCESS</span><span class="bottom">MEMBER</span></div>
  </div>

  <section class="card" style="left:51px">
    <ul class="perks" style="margin-top:10px">
      <li>Use of Hot Desks &amp;<br>Lounge Areas</li>
      <li>Secure Wifi</li>
      <li>Free Tea &amp; Coffee</li>
    </ul>
    <div class="price" style="top:228px">
      <span class="pill"><sup>£</sup>25.00</span>
      <span class="price-note">Each<br>visit</span>
    </div>
    <div class="price-sub" style="top:280px">Price Inclusive of VAT | Each Visit</div>
  </section>

  <section class="card mid" style="left:290px">
    <ul class="perks" style="margin-top:8px">
      <li>Use of Hot Desks &amp;<br>Lounge Areas</li>
      <li>Secure Wifi</li>
      <li>Free Tea &amp; Coffee</li>
      <li>Discounted E/V Charge Rates</li>
      <li>Access to Meeting Rooms<small>(£10+vat per person, per hour)</small></li>
    </ul>
    <div class="price" style="top:226px">
      <span class="pill"><sup>£</sup>18</span>
      <span class="plus">+</span>
      <span class="pill"><sup>£</sup>18</span>
    </div>
    <div class="price-labels" style="top:268px"><span>a month</span><span>Each Visit</span></div>
    <div class="price-sub" style="top:290px">Price Inclusive of VAT | Per month</div>
  </section>

  <section class="card" style="left:526px;padding-top:18px">
    <ul class="perks">
      <li>Unlimited Number of Visits<br>Each Month</li>
      <li>Dedicated Desk<small>(lockable draws + £60 a month)</small></li>
      <li>Receptionist to Meet &amp;<br>Greet Guests</li>
      <li>Use of Lounge Areas</li>
      <li>Secure Wifi</li>
      <li>Free Tea &amp; Coffee</li>
      <li>Discounted E/V Charge Rates</li>
      <li>Access to Meeting Rooms<small>(£10+vat per person, per hour)</small></li>
    </ul>
    <div class="price" style="top:254px">
      <span class="pill"><sup>£</sup>180.00</span>
    </div>
    <div class="price-sub" style="top:300px">Price Inclusive of VAT | Per month</div>
  </section>

  <footer class="footer">
    <div class="email">
      <svg width="16" height="12" viewBox="0 0 16 12"><rect width="16" height="12" rx="1" fill="var(--orange)"/><path d="M1 1l7 6 7-6" fill="none" stroke="#fff" stroke-width="1.4"/></svg>
      info@tealantern.co.uk
    </div>
    <span class="divider"></span>
    <div class="web">www.<b>tealantern</b>.co.uk</div>
  </footer>
</main>
</body>
</html>
```